Telecommunications/Power civil contractor needs business card design

Were a new telecommunications/power underground civil contractor that is looking for a new business card design. Our company colours are silver or grey and orange. Feel free to use the white background logo or the black background logo.

Target Market(s)

Local contractors, utility companies, private sector mining/energy companies, developers.

Industry/Entity Type

Telecommunications

Contact Information for Business Card

Each card will need the following info:
Persons name:
Title:
E-mail:
Phone number:
Shop Address:
Mailing Address:

Requirements
Must have
• Each card will need the following info:
• Persons name:
• Title:
• E-mail:
• Phone number:
• Shop Address:
• Mailing Address:

```html
<!DOCTYPE html>
<html lang="en">
<head>
<meta charset="utf-8">
<title>Ridgeline Contracting Inc – Business Card</title>
<link rel="stylesheet" href="https://fonts.googleapis.com/css2?family=Montserrat:wght@400;500;700&display=swap">
<style>
  :root {
    --backdrop: #e9e6e1;
    --card: #ffffff;
    --orange: #ec6a2c;
    --grey: #6f6f6f;
    --grey-light: #9a9a9a;
    --rule: #c4c4c4;
  }
  * { margin: 0; padding: 0; box-sizing: border-box; }
  html, body {
    width: 1200px; height: 1022px; overflow: hidden;
    background: var(--backdrop);
    font-family: "Montserrat", sans-serif;
  }
  .card {
    position: absolute; left: 150px; top: 254px;
    width: 900px; height: 514px;
    background: var(--card);
    border-radius: 18px;
    box-shadow: 0 10px 30px rgba(0,0,0,0.12);
    display: flex; align-items: center;
  }
  .brand {
    width: 420px; display: flex; align-items: center; justify-content: center; gap: 22px;
  }
  .brand-dot {
    width: 70px; height: 70px; border-radius: 50%; background: var(--orange); flex: none;
  }
  .brand-name {
    font-weight: 700; color: var(--grey); text-transform: uppercase;
    font-size: 30px; line-height: 1.15; letter-spacing: 0.5px;
  }
  .divider {
    width: 2px; height: 300px; background: var(--rule);
  }
  .contact {
    padding-left: 52px; color: var(--grey);
  }
  .contact-name {
    font-weight: 700; color: var(--orange); font-size: 34px; letter-spacing: 1px;
  }
  .contact-title {
    font-size: 19px; margin-top: 2px; margin-bottom: 22px;
  }
  .address { font-size: 19px; line-height: 1.5; margin-bottom: 18px; }
  .address-mail { text-transform: uppercase; }
  .lines { list-style: none; font-size: 19px; line-height: 1.55; }
  .lines li { display: flex; align-items: center; gap: 14px; }
  .lines svg { width: 17px; height: 17px; flex: none; stroke: var(--orange); fill: none; stroke-width: 1.8; }
</style>
</head>
<body>
  <section class="card">
    <div class="brand">
      <span class="brand-dot"></span>
      <div class="brand-name">Ridgeline<br>Contracting Inc</div>
    </div>
    <div class="divider"></div>
    <div class="contact">
      <h1 class="contact-name">MARCO ELLIS</h1>
      <p class="contact-title">Director</p>
      <p class="address address-mail">PO BOX 4186<br>LAKE HOLLOW, CA 91520</p>
      <p class="address address-shop">48 Foundry Lane<br>Harlow Point, NY 12590</p>
      <ul class="lines">
        <li><svg viewBox="0 0 16 16"><rect x="4" y="1" width="8" height="14" rx="1.5"/><line x1="7" y1="12.5" x2="9" y2="12.5"/></svg>+330 5182-4403</li>
        <li><svg viewBox="0 0 16 16"><path d="M3 2l3 0 1 3.5-2 1.3a8 8 0 0 0 4.2 4.2L10.5 9l3.5 1v3a1 1 0 0 1-1 1A12 12 0 0 1 2 3a1 1 0 0 1 1-1z"/></svg>+330 5182-4419</li>
        <li><svg viewBox="0 0 16 16"><rect x="1.5" y="3.5" width="13" height="9" rx="1"/><path d="M1.5 4l6.5 5 6.5-5"/></svg>info@ridgelinecontracting.com</li>
        <li><svg viewBox="0 0 16 16"><circle cx="8" cy="8" r="6.5"/><ellipse cx="8" cy="8" rx="2.8" ry="6.5"/><line x1="1.5" y1="8" x2="14.5" y2="8"/></svg>www.ridgelinecontracting.com</li>
      </ul>
    </div>
  </section>
</body>
</html>
```